Constant Contact email marketing template

I need engaging customizable templates that can be used in multiple fundraising campaigns.

I included a school bus project that we used in a previous campaign. This campaign, however, is a $25 for $25 promotion. Consumers make a $25 contribution for the school or charity and receive back a $25 e-gift card to be used at area restaurants.

Important! This is a completely generic piece, capable of being used in schools, churches, or other civic organizations.

The 5 part example is NOT what I am looking for. I included it to suggest the concept. I am looking forward to viewing YOUR designs,

Target Market(s)

schools, leagues, nonprofit organizations

Font styles to use
Sans Serif

Colors

Designer to choose colors to be used in the design.

Requirements
Must have
• Must clearly present itself as a fundraising tool for schools, leagues and Nonprofit organizations.
• Must have 2 clickable buttons that allow member to click

```html
<!DOCTYPE html>
<html lang="en">
<head>
<meta charset="utf-8">
<title>$25 for $25 Fundraiser Email</title>
<link rel="stylesheet" href="https://fonts.googleapis.com/css2?family=Open+Sans:wght@400;600;700;800&family=Oswald:wght@300;400&family=Roboto+Condensed:wght@400&family=Kaushan+Script&family=Montserrat:wght@800;900&display=swap">
<style>
  :root {
    --red-deep: #9d0f17;
    --red: #b3141c;
    --art-pink: #cf3552;
    --art-rose: #a8162a;
    --yellow: #ffe566;
    --white: #ffffff;
    --btn-red-top: #e9452a;
    --btn-red-bottom: #b8141a;
    --btn-gold-top: #f2c12a;
    --btn-gold-bottom: #db8f1e;
    --btn-rim: #e6e6e6;
    --sky: #84c3e0;
    --ink: #1c1c1c;
    --grey: #6f6f6f;
    --rule: #8a8a8a;
  }
  * { box-sizing: border-box; margin: 0; padding: 0; }
  html, body { width: 1200px; height: 2453px; overflow: hidden; background: var(--white); }
  .email { position: relative; width: 1200px; height: 2453px; font-family: "Open Sans", sans-serif; }

  .hero-band {
    position: absolute; left: 0; top: 0; width: 1200px; height: 1703px;
    background: radial-gradient(ellipse at 50% 35%, var(--red) 0%, var(--red-deep) 80%);
  }

  .org-name {
    position: absolute; left: 49px; top: 68px; width: 450px;
    color: var(--white); font-weight: 700;
    font-size: 50px; letter-spacing: 1px; line-height: 1; text-align: center;
  }
  .org-name small { display: block; font-size: 20px; font-weight: 700; letter-spacing: 5px; margin-top: 14px; }

  .title-rule { position: absolute; left: 540px; top: 72px; width: 345px; height: 4px; background: var(--white); }
  .title-greatest {
    position: absolute; left: 925px; top: 28px; color: var(--white);
    font-family: "Kaushan Script", cursive; font-size: 50px; line-height: 1;
  }
  .title-main {
    position: absolute; left: 697px; top: 100px; color: var(--white);
    font-family: "Montserrat", sans-serif; font-weight: 800; font-size: 36px;
    letter-spacing: 16px; line-height: 1;
  }
  .title-ever {
    position: absolute; left: 925px; top: 140px; color: var(--white);
    font-family: "Kaushan Script", cursive; font-size: 96px; line-height: 1;
    transform: rotate(-8deg);
  }

  .offer-art {
    position: absolute; left: 88px; top: 250px; width: 1032px; height: 590px;
    border-radius: 24px;
    background: radial-gradient(ellipse at 50% 50%, var(--art-pink) 0%, var(--art-rose) 75%);
  }

  .headline {
    position: absolute; left: 0; top: 875px; width: 1200px; text-align: center;
    color: var(--white); font-weight: 700; font-size: 53px; line-height: 57px;
  }
  .subline {
    position: absolute; left: 180px; top: 1076px; width: 840px; text-align: center;
    color: var(--white); font-size: 21px; letter-spacing: 2px; line-height: 25px; text-transform: uppercase;
  }
  .checklist { position: absolute; left: 300px; top: 1150px; list-style: none; }
  .checklist li {
    display: flex; align-items: center; height: 52px;
    color: var(--yellow); font-weight: 700; font-size: 33px;
  }
  .checklist svg { width: 40px; height: 40px; margin-right: 8px; }

  .btn {
    position: absolute; left: 182px; width: 820px; height: 188px; border-radius: 60px;
    display: flex; align-items: center; justify-content: center; text-decoration: none;
    border: 7px solid var(--btn-rim);
    box-shadow: 0 10px 18px rgba(0,0,0,.35), inset 0 4px 10px rgba(255,255,255,.35);
    font-family: "Oswald", sans-serif; font-weight: 300; text-transform: uppercase;
  }
  .btn-donate { top: 1358px; background: linear-gradient(var(--btn-red-top), var(--btn-red-bottom)); color: var(--white); font-size: 82px; }
  .btn-tribute { top: 1607px; background: linear-gradient(var(--btn-gold-top), var(--btn-gold-bottom)); color: #4a4a4a; font-size: 42px; }

  .offer-title {
    position: absolute; left: 0; top: 1840px; width: 1200px; text-align: center;
    color: var(--sky); font-weight: 700; font-size: 68px; line-height: 1;
  }
  .offer-body {
    position: absolute; left: 161px; top: 1938px; width: 845px;
    color: var(--ink); font-family: "Roboto Condensed", sans-serif; font-size: 23px; line-height: 33px;
  }

  .contact-row {
    position: absolute; left: 100px; top: 2136px; width: 1010px;
    display: flex; align-items: center; justify-content: space-between;
    color: var(--grey); font-size: 27px;
  }
  .contact-row b { font-weight: 700; }
  .social { display: flex; gap: 16px; }
  .social span { width: 34px; height: 34px; border-radius: 50%; background: var(--grey); }

  .footer-rule { position: absolute; left: 28px; top: 2198px; width: 1135px; height: 2px; background: var(--rule); }
  .footer {
    position: absolute; left: 0; top: 2285px; width: 1200px; text-align: center;
    color: #222; font-size: 15px; letter-spacing: 6px; line-height: 21px; text-transform: uppercase;
  }
  .footer p:first-child { margin-bottom: 22px; }
</style>
</head>
<body>
<main class="email">
  <div class="hero-band"></div>

  <div class="org-name">MAPLECREST<small>School District</small></div>

  <div class="title-rule"></div>
  <div class="title-greatest">greatest</div>
  <div class="title-main">FUNDRAISER</div>
  <div class="title-ever">ever!</div>

  <div class="offer-art" role="img" aria-label="Illustration of two marquee-light arrows reading: $25 contribution, you get a $25 e-gift card"></div>

  <h1 class="headline">Simply donate $25 and we give<br>you $25 back in e-Gift Cards for<br>restaurants in your area!</h1>
  <p class="subline">"Sed ut perspiciatis unde omnis iste natus error sit voluptatem ac</p>

  <ul class="checklist">
    <li><svg viewBox="0 0 40 40"><path d="M4 22 L15 34 L37 5 L16 24 Z" fill="#e8263a"/></svg>"Sed ut perspiciatis unde omnis.</li>
    <li><svg viewBox="0 0 40 40"><path d="M4 22 L15 34 L37 5 L16 24 Z" fill="#e8263a"/></svg>"Sed ut perspiciatis unde omnis.</li>
    <li><svg viewBox="0 0 40 40"><path d="M4 22 L15 34 L37 5 L16 24 Z" fill="#e8263a"/></svg>"Sed ut perspiciatis unde omnis.</li>
  </ul>

  <a class="btn btn-donate" href="#donate">Donate Now!</a>
  <a class="btn btn-tribute" href="#donate-tribute">Donate on behalf of a loved one or friend</a>

  <h2 class="offer-title">$25 for $25</h2>
  <p class="offer-body">"Sed ut perspiciatis unde omnis iste natus error sit voluptatem accusantium doloremque laudantium, totam rem aperiam, eaque ipsa quae ab illo inventore veritatis et quasi architecto beatae vitae dicta sunt explicabo. Nemo enim ipsam voluptatem quia voluptas sit aspernatur aut odit aut fugit, sed quia consequuntur magni dolores eos qui ratione voluptatem sequi nesciunt.</p>

  <div class="contact-row">
    <span>www.<b>maplecrestgives</b>.org</span>
    <span class="social"><span></span><span></span><span></span></span>
    <span>Phone 12345687 - email@email.com</span>
  </div>

  <div class="footer-rule"></div>
  <footer class="footer">
    <p>Text Inc - Adress here number 1234 - 012346</p>
    <p>Unsubscribe - here</p>
    <p>Update profile - about our service provider</p>
    <p>Sent by support@dinegive.org in collaboration with</p>
  </footer>
</main>
</body>
</html>
```